Website design for legal tech start up in Switzerland (B2B)

We are for a legal tech start up in Switzerland called KOVA. We have been running since August 2016. This will be our first live website.

We need a website designed and business card design for our start-up in Switzerland. We also need the Web design to be converted into HTML and CSS files.

Function of website:
• To inform potential customers of our services
• Form a key part of our digital marketing and sales footprint.
• Branding

Please find attached logo.
Updates

Project Deadline Extended Reason: Giving us time to review submissions and provide opportunity for more submissions. Added Thursday, February 16, 2017

Project Deadline Extended
Reason: Looking for more idea's not necessarily set on blue and grey colours only.

Target Market(s)

B2B tech powered legal services.

Industry/Entity Type

Legal

Contact Information for Business Card

Lean and slick design.

Coding

Coded - Design and coding required

Number of Pages Required

5+ page

Requirements
Must have
• VERY LEAN AND CLEAN DESIGN!
• We have received many great standard designs, but we are looking for something more out-of-the box: You can get inspiration from these designs: http://www.pixelvane.com/websites/clean/
• Thanks!!
• Easy content management system
• Well structured coding for additional development
• Responsive webpage for all types of devices
• SEO optimized
• Tabs (Home, services, team, careers, blog, contact us)
• Colour scheme complementary to logo
Nice to have
• Look and Design - Approachable, High-tech, Modern
• Easy to add chat bot capability in future
Should not have
• Too busy/ too much clutter
• Not take to long to load

```html
<!DOCTYPE html>
<html lang="en">
<head>
<meta charset="utf-8">
<title>KOVA – Legal Startup</title>
<link href="https://fonts.googleapis.com/css2?family=Roboto:wght@400;500;700&display=swap" rel="stylesheet">
<style>
:root{
  --navy:#1d3d6f;
  --navy-dark:#162f57;
  --ink:#333a44;
  --text:#555c66;
  --muted:#8a9099;
  --grey-btn:#6b6d70;
  --icon-grey:#5e6064;
  --page:#f4f5f8;
  --white:#ffffff;
  --line:#dfe2e7;
}
*{box-sizing:border-box;margin:0;padding:0}
html,body{width:674px;height:1200px;overflow:hidden}
body{position:relative;background:var(--page);font-family:'Roboto',Arial,sans-serif;color:var(--text)}
.abs{position:absolute}
/* header */
.site-header{left:0;top:0;width:674px;height:49px;background:var(--white)}
.brand{left:47px;top:12px;font-size:26px;font-weight:700;letter-spacing:1px;color:var(--ink)}
.nav a{position:absolute;top:23px;font-size:6.6px;font-weight:500;color:#444;text-decoration:none;white-space:nowrap}
.nav a.active{color:var(--navy)}
/* hero */
.hero{left:0;top:49px;width:674px;height:271px;background:linear-gradient(180deg,#7f9dbe 0%,#a9b6b8 30%,#7d8a6c 50%,#4f8796 70%,#2f6f82 100%)}
.hero-band{left:0;top:320px;width:674px;height:10px;background:#4b4c4f}
.hero-title{left:0;top:192px;width:674px;text-align:center;color:var(--white);font-size:18px;font-weight:500;letter-spacing:.3px}
.hero-sub{left:180px;top:221px;width:314px;text-align:center;color:var(--white);font-size:6.3px;line-height:12.5px}
.hero-arrow{width:28px;height:28px;top:176px;border:1.5px solid var(--white);border-radius:50%}
/* feature cards */
.features{left:48px;top:293px;width:578px;height:169px;background:var(--white);box-shadow:0 1px 3px rgba(0,0,0,.12)}
.feature{width:192px;text-align:center}
.feature.raised{left:241px;top:271px;height:145px;background:var(--white);box-shadow:0 3px 8px rgba(0,0,0,.18)}
.feature-icon{width:56px;height:56px;border-radius:50%;background:var(--icon-grey);margin:0 auto}
.raised .feature-icon{background:var(--navy);border:2px solid var(--white);box-shadow:0 0 0 1.5px var(--navy)}
.feature h3{font-size:8.8px;font-weight:400;color:var(--ink);margin-top:10px;letter-spacing:.2px}
.raised h3{color:var(--navy);font-weight:500}
.feature p{font-size:6.3px;line-height:13px;margin:6px auto 0;width:150px}
.btn{display:inline-block;color:var(--white);font-size:6.6px;font-weight:500;text-align:center;line-height:20px}
.btn-grey{background:var(--grey-btn);width:64px}
.btn-navy{background:var(--navy);width:64px}
/* welcome / team */
.section-title{font-size:11.5px;font-weight:400;color:var(--ink);letter-spacing:.2px}
.section-title b{color:var(--navy);font-weight:500}
.body-copy{font-size:6.3px;line-height:13px;color:var(--text)}
.team-photo{left:286px;top:517px;width:72px;height:72px;border-radius:50%;background:radial-gradient(circle at 50% 40%,#c99a82 0%,#6f4a3a 60%,#3a2a24 100%)}
.quote-mark{font-size:14px;color:var(--muted);font-weight:700}
/* blog */
.blog{left:0;top:646px;width:674px;height:303px;background:var(--white)}
.post-img{width:183px;height:116px}
.post-title{font-size:9.5px;color:var(--ink);font-weight:400}
.post-meta{font-size:4.6px;color:var(--muted);width:183px;border-top:1px solid var(--line);border-bottom:1px solid var(--line);height:17px;line-height:15px;display:flex;justify-content:space-between;padding:0 2px}
.post-text{font-size:6.3px;line-height:13.5px;width:183px}
/* partners */
.partners{left:0;top:949px;width:674px;height:65px;background:var(--navy)}
.partner{top:12px;width:80px;height:43px;border:1px solid rgba(255,255,255,.35);color:var(--white);font-size:10.5px;font-weight:500;display:flex;align-items:center;justify-content:center;gap:5px}
.partner i{width:9px;height:9px;background:var(--white);display:block}
/* footer */
.foot-brand{left:55px;top:1070px;font-size:40px;font-weight:700;letter-spacing:2px;color:var(--ink)}
.foot-title{font-size:8.8px;color:var(--ink);font-weight:400}
.contact-item{font-size:6.3px;color:var(--text);display:flex;gap:8px;align-items:flex-start;line-height:8px}
.contact-item svg{flex:none}
.email-field{left:367px;top:1093px;width:119px;height:18px;background:var(--white);border:1px solid #ccd;font-size:6.3px;line-height:16px;padding-left:8px;color:#666}
.subscribe{left:368px;top:1121px;width:45px;height:15px;background:var(--navy-dark);color:var(--white);font-size:5.6px;line-height:15px;text-align:center;font-weight:500}
.social{top:1109px;width:20px;height:20px;border:1px solid #b8bcc3;border-radius:50%}
.foot-rule{left:48px;top:1165px;width:578px;height:1px;background:var(--line)}
.copyright{left:0;top:1178px;width:674px;text-align:center;font-size:6.6px;color:#444}
</style>
</head>
<body>

<header class="site-header abs">
  <div class="brand abs">KOVA</div>
  <nav class="nav">
    <a class="active" style="left:319px">HOME</a>
    <a style="left:368px">SERVICES</a>
    <a style="left:430px">TEAM</a>
    <a style="left:478px">CAREERS</a>
    <a style="left:537px">BLOG</a>
    <a style="left:585px">CONTACT US</a>
  </nav>
</header>

<section class="hero abs" role="img" aria-label="Photo of a Swiss old town along a river with church towers and boats"></section>
<div class="hero-band abs"></div>
<h1 class="hero-title abs">LEGAL STARTUP</h1>
<p class="hero-sub abs">Sed ut perspiciatis unde omnis iste natus error sit voluptatem accusa ntium doloremque laudantium, totam rem aperiam, eaque ipsa quae ab illo inventore veritatis et quasi</p>
<div class="hero-arrow abs" style="left:15px"><svg width="25" height="25" viewBox="0 0 25 25"><path d="M14 8l-5 4.5 5 4.5" fill="none" stroke="#fff" stroke-width="1.8"/></svg></div>
<div class="hero-arrow abs" style="left:631px"><svg width="25" height="25" viewBox="0 0 25 25"><path d="M11 8l5 4.5-5 4.5" fill="none" stroke="#fff" stroke-width="1.8"/></svg></div>

<div class="features abs"></div>
<div class="feature abs" style="left:45px;top:300px">
  <div class="feature-icon"><svg width="56" height="56" viewBox="0 0 56 56"><circle cx="30" cy="23" r="7" fill="none" stroke="#fff" stroke-width="3" stroke-dasharray="3 2"/><circle cx="30" cy="23" r="3" fill="#fff"/><path d="M14 36h8l8 3 10-5v4l-10 6-16-2z" fill="#fff"/></svg></div>
  <h3>SERVICES</h3>
  <p>Sed ut perspiciatis unde omnis iste natus error sit voluptatem accusantium doloremque laube atae vitae dicta sunt explicabo.</p>
  <span class="btn btn-grey" style="margin-top:6px">READ MORE</span>
</div>
<div class="feature raised abs">
  <div style="height:17px"></div>
  <div class="feature-icon"><svg width="52" height="52" viewBox="0 0 52 52"><path d="M19 14h11l5 5v19H19z" fill="none" stroke="#fff" stroke-width="1.6"/><path d="M23 22h8M23 26h8M23 30h5" stroke="#fff" stroke-width="1.2"/><circle cx="30" cy="34" r="2" fill="#fff"/></svg></div>
  <h3>LEGAL</h3>
  <p>Sed ut perspiciatis unde omnis iste natus error sit voluptatem accusantium doloremque laube atae vitae dicta sunt explicabo.</p>
  <span class="btn btn-navy" style="margin-top:6px">READ MORE</span>
</div>
<div class="feature abs" style="left:437px;top:300px">
  <div class="feature-icon"><svg width="56" height="56" viewBox="0 0 56 56"><circle cx="31" cy="15" r="3.5" fill="#fff"/><path d="M29 20l-6 7 5 2-3 9M30 21l5 6h5M27 28l7 4" fill="none" stroke="#fff" stroke-width="3" stroke-linecap="round"/><rect x="15" y="25" width="8" height="6" fill="#fff"/><path d="M32 42h5v-4h5v-4h5" fill="none" stroke="#fff" stroke-width="2"/></svg></div>
  <h3>CAREERS</h3>
  <p>Sed ut perspiciatis unde omnis iste natus error sit voluptatem accusantium doloremque laube atae vitae dicta sunt explicabo.</p>
  <span class="btn btn-grey" style="margin-top:6px">READ MORE</span>
</div>

<h2 class="section-title abs" style="left:48px;top:488px">WELCOME TO <b>KOVA</b></h2>
<p class="body-copy abs" style="left:48px;top:514px;width:214px">Sed ut perspiciatis unde omnis iste natus error sit voluptatem accusa ntium doloremque laudantium, totam rem aperiam, eaque ipsa quae ab illo inventore veritatis et quasi architecto beatae vitae dicta sunt exp licabo. Nemo enim ipsam voluptatem quia voluptas sit aspernatur aut odit aut fugit, sed quia consequuntur magni dolores eos qui ratione beatae vitae dicta voluptatem sequi nesciunt.</p>
<span class="btn btn-navy abs" style="left:48px;top:607px;width:70px;line-height:21px">READ MORE</span>

<h2 class="section-title abs" style="left:287px;top:488px">OUR <b>TEAM</b></h2>
<div class="team-photo abs" role="img" aria-label="Portrait photo of a team member"></div>
<span class="quote-mark abs" style="left:368px;top:522px">&ldquo;</span>
<p class="body-copy abs" style="left:379px;top:532px;width:244px">Sed ut perspiciatis unde omnis iste natus error sit voluptatem accusantium dolo-remque laudantium, totam rem aperiam, eaque ipsa quae ab illo inventore verita-tis et quasi architecto beatae vitae dicta sunt explicabo. Nemo enim ipsam volup-tatem quia voluptas sit aspernatur aut odit aut fugit</p>
<span class="quote-mark abs" style="left:537px;top:577px">&rdquo;</span>
<p class="abs" style="left:380px;top:600px;font-size:7px;font-weight:500;color:var(--navy)">Name : Lena Brunner</p>
<p class="abs" style="left:380px;top:613px;font-size:5.6px;color:var(--muted)">Posed on 02 January 2017</p>

<section class="blog abs">
  <h2 class="section-title abs" style="left:0;top:16px;width:674px;text-align:center;font-size:14px">LATEST <b>BLOG</b></h2>
  <p class="abs" style="left:0;top:44px;width:674px;text-align:center;font-size:6.3px">Sed ut perspiciatis unde omnis iste natus error sit voluptatem accusantium doloremque laudantium</p>
</section>

<div class="post-img abs" style="left:48px;top:713px;background:linear-gradient(135deg,#3b3d40,#d8d9da 55%,#8f8a84)" role="img" aria-label="Photo of business people signing documents at a table"></div>
<div class="post-img abs" style="left:245px;top:713px;background:linear-gradient(135deg,#4a3b33,#a48d7c 55%,#d6c8bb)" role="img" aria-label="Photo of a hand signing a contract with a pen"></div>
<div class="post-img abs" style="left:443px;top:713px;background:linear-gradient(135deg,#5d6f80,#e6e9ec 50%,#9aa4ad)" role="img" aria-label="Photo of a businessman reviewing papers next to a laptop"></div>

<h3 class="post-title abs" style="left:48px;top:843px">Sed ut perspiciatis unde</h3>
<h3 class="post-title abs" style="left:245px;top:843px">Sed ut perspiciatis unde</h3>
<h3 class="post-title abs" style="left:443px;top:843px">Sed ut perspiciatis unde</h3>

<div class="post-meta abs" style="left:48px;top:863px"><span>◷ 27 MARCH 2017</span><span>◌ 120</span><span>♡ LIKE</span><span>↗ SHARE</span></div>
<div class="post-meta abs" style="left:245px;top:863px"><span>◷ 27 MARCH 2017</span><span>◌ 120</span><span>♡ LIKE</span><span>↗ SHARE</span></div>
<div class="post-meta abs" style="left:443px;top:863px"><span>◷ 27 MARCH 2017</span><span>◌ 120</span><span>♡ LIKE</span><span>↗ SHARE</span></div>

<p class="post-text abs" style="left:48px;top:889px">Sed ut perspiciatis unde omnis iste natus error sit volupta-tem accusantium doloremque laudantium, totam rem aperi architecto beatae vitae dicta sunt explicabo.</p>
<p class="post-text abs" style="left:245px;top:889px">Sed ut perspiciatis unde omnis iste natus error sit volupta-tem accusantium doloremque laudantium, totam rem aperi architecto beatae vitae dicta sunt explicabo.</p>
<p class="post-text abs" style="left:443px;top:889px">Sed ut perspiciatis unde omnis iste natus error sit volupta-tem accusantium doloremque laudantium, totam rem aperi architecto beatae vitae dicta sunt explicabo.</p>

<section class="partners abs">
  <div class="partner abs" style="left:48px">Northgate</div>
  <div class="partner abs" style="left:148px">Valtiq</div>
  <div class="partner abs" style="left:247px">Sonora</div>
  <div class="partner abs" style="left:347px"><i></i>Quadrel</div>
  <div class="partner abs" style="left:446px"><i></i>Brightwell</div>
  <div class="partner abs" style="left:546px">Framecraft</div>
</section>

<footer>
  <div class="foot-brand abs">KOVA</div>

  <h4 class="foot-title abs" style="left:212px;top:1042px">CONTACT US</h4>
  <div class="contact-item abs" style="left:212px;top:1068px"><svg width="8" height="8" viewBox="0 0 8 8"><path d="M1 3c0-2 6-2 6 0v1H5V3H3v1H1zM2 5h4v2H2z" fill="#777"/></svg>(000)-484-2076 (Phone)</div>
  <div class="contact-item abs" style="left:212px;top:1085px"><svg width="8" height="8" viewBox="0 0 8 8"><rect x="2" y="0.5" width="4" height="2.5" fill="#777"/><rect x="0.5" y="3" width="7" height="3.5" fill="#777"/></svg>(000)-484-2077 (Fax)</div>
  <div class="contact-item abs" style="left:212px;top:1101px"><svg width="8" height="8" viewBox="0 0 8 8"><rect x="0.5" y="1.5" width="7" height="5" fill="#777"/><path d="M0.5 1.5L4 4.5 7.5 1.5" fill="none" stroke="#fff" stroke-width=".8"/></svg><span style="text-decoration:underline">www.kova-legal.ch</span></div>
  <div class="contact-item abs" style="left:212px;top:1117px"><svg width="8" height="8" viewBox="0 0 8 8"><path d="M4 8L1.5 4A2.6 2.6 0 1 1 6.5 4z" fill="#777"/></svg><span>3350 Lorem Ipsum Dummy Text<br>Lorem Ipsum</span></div>

  <h4 class="foot-title abs" style="left:367px;top:1042px">NEWSLETTER</h4>
  <p class="abs" style="left:367px;top:1065px;width:125px;font-size:6.3px;line-height:11px">Register Your email address to get information about us</p>
  <div class="email-field abs">Email Address</div>
  <div class="subscribe abs">SUBSCRIBE</div>

  <h4 class="foot-title abs" style="left:510px;top:1042px">FOLLOW US</h4>
  <p class="abs" style="left:510px;top:1067px;width:126px;font-size:6.3px;line-height:10.5px">Lorem ipsum dolor sit amet, conse ctetur adipiscing elit. Nulla in purus nibh. Donec ornare</p>
  <div class="social abs" style="left:509px" aria-label="Social profile"></div>
  <div class="social abs" style="left:533px" aria-label="Social profile"></div>
  <div class="social abs" style="left:557px" aria-label="Social profile"></div>
  <div class="social abs" style="left:581px" aria-label="Social profile"></div>
  <div class="social abs" style="left:605px" aria-label="Social profile"></div>

  <div class="foot-rule abs"></div>
  <p class="copyright abs">© Copyright 2017 KOVA All Rights Reserved</p>
</footer>

</body>
</html>
```